Tessaro Mobile website

Hello. Pray all is well. Peace be with you.

looking to make a website with pages information from https://veradilo.us. English and Spanish.

the header of quarnetel.com when in mobile version

clean vector images and layout of fendlecell.com

and the clean simple black and white look of tavesport.com

please use the attached logo for color guidance

also need the my account section for users to be designed

there should also be a countdown timer for days:hours:seconds on the home page

please do website in figma

```html
<!DOCTYPE html>
<html lang="en">
<head>
<meta charset="utf-8">
<title>Tessaro Mobile</title>
<link href="https://fonts.googleapis.com/css2?family=League+Spartan:wght@400;500;600&family=Kumbh+Sans:wght@400;500;600&display=swap" rel="stylesheet">
<style>
:root{
  --bg:#0b0b0b;
  --panel:#1b1a18;
  --band:#1c1b19;
  --gold:#c2a462;
  --gold-deep:#a68c52;
  --gold-text:#c9aa5c;
  --white:#ffffff;
  --muted:#bdbdbd;
  --line:#4a463d;
}
*{margin:0;padding:0;box-sizing:border-box}
html,body{width:1200px;height:3975px;overflow:hidden;background:var(--bg)}
body{font-family:"Kumbh Sans",sans-serif;color:var(--white);position:relative}
.abs{position:absolute}
.head{font-family:"League Spartan",sans-serif;font-weight:500;text-transform:uppercase;letter-spacing:.2px}
.gold{color:var(--gold-text)}
.brand{display:flex;align-items:center;gap:8px;white-space:nowrap}
.brand-dot{width:12px;height:12px;border-radius:50%;background:var(--gold);flex:none}
.brand-name{font-family:"League Spartan",sans-serif;font-weight:500;color:var(--white);font-size:18px;line-height:1}
/* header */
.site-nav{left:318px;top:42px;display:flex;gap:22px;font-size:13px;font-family:"League Spartan",sans-serif;text-transform:uppercase;white-space:nowrap}
.site-nav .active{color:var(--gold-text)}
.account-btn{left:946px;top:34px;width:106px;height:32px;background:var(--gold-deep);font-size:11px;display:flex;align-items:center;justify-content:center;border-radius:3px;font-family:"League Spartan",sans-serif}
.lang{left:1076px;top:42px;font-size:13px;font-family:"League Spartan",sans-serif}
/* hero */
.hero-card{left:82px;top:97px;width:1036px;height:412px;border-radius:20px;background:linear-gradient(110deg,#1e1d1b 0%,#141413 55%,#2a261c 100%)}
.hero-kicker{left:148px;top:176px;font-size:15px}
.hero-title{left:148px;top:222px;font-size:27px;line-height:44px;width:430px}
.countdown{left:146px;top:375px;display:flex;gap:28px;align-items:flex-start}
.cd-unit{text-align:center}
.cd-num{font-family:"League Spartan",sans-serif;font-size:42px;color:var(--gold-text);line-height:1}
.cd-label{font-size:8px;color:var(--muted);margin-top:10px}
.cd-sep{font-size:36px;color:var(--white);line-height:1;margin-top:4px}
.hero-art{left:617px;top:108px;width:395px;height:440px;border-radius:30px;background:radial-gradient(circle at 40% 45%,#c89a3c 0%,#8c6a2f 30%,#e8e4da 55%,#2a2722 85%)}
/* features */
.feature{width:234px;height:217px;top:623px;background:var(--panel);border-radius:6px;display:flex;flex-direction:column;align-items:center;justify-content:center;text-align:center;gap:22px;font-size:17px;line-height:35px}
.feature svg{width:64px;height:64px}
.feature.highlight{background:linear-gradient(140deg,#8a6a3c,#4d3a22 60%,#a88a58)}
/* check */
.check-band{left:0;top:925px;width:1200px;height:420px;background:linear-gradient(90deg,#1b1a18,#242220 50%,#1a1917)}
.section-title{left:0;width:1200px;text-align:center;font-size:28px}
.mascot{background:radial-gradient(circle,#b8b2a6,#6c675f 60%,#c76a2a);border-radius:50%}
.check-panel{left:162px;top:1044px;width:876px;height:239px;border-radius:0 0 22px 0;display:flex}
.check-left{width:436px;height:100%;background:linear-gradient(90deg,rgba(31,30,28,0),#1f1e1c 40%)}
.check-right{width:440px;height:100%;background:#2b2a26;border-radius:0 0 22px 0}
.check-input{top:1190px;height:39px;font-size:11px;display:flex;align-items:center;padding-left:14px;font-family:"League Spartan",sans-serif}
/* steps */
.step-num{font-family:"League Spartan",sans-serif;font-size:62px;color:#1d1a14;font-weight:600}
.step-title{font-size:17px;line-height:33px;color:var(--gold-text)}
.step-desc{font-size:13.5px;line-height:30px}
.phone-frame{left:506px;top:1531px;width:188px;height:381px;border:3px solid #cfcfcf;border-radius:26px;background:#0e0e0e}
/* reviews */
.review-band{left:0;top:2028px;width:1200px;height:458px;background:var(--band)}
.review{top:2159px;width:294px;height:259px;background:#161615;padding:34px 26px}
.stars{color:#f5c542;font-size:18px;letter-spacing:3px}
.review p{font-size:13.5px;line-height:30px;margin-top:20px}
.reviewer{display:flex;align-items:center;gap:20px;margin-top:20px;font-family:"League Spartan",sans-serif;font-size:15px;font-weight:500}
.avatar{width:46px;height:46px;border-radius:50%;background:linear-gradient(#8a6a50,#dcd2c4)}
/* faq */
.faq{width:431px;height:44px;border-bottom:1px solid var(--line);display:flex;justify-content:space-between;align-items:flex-start;font-size:13px;font-family:"League Spartan",sans-serif;text-transform:uppercase}
.faq svg{flex:none}
.faq-btn{left:484px;top:2991px;width:232px;height:44px;background:var(--gold-deep);font-size:15px;display:flex;align-items:center;justify-content:center;border-radius:3px}
/* posts */
.post{top:3200px;width:316px;height:362px;background:var(--panel);border-radius:10px;overflow:hidden}
.post-img{height:208px}
.post-meta{display:flex;justify-content:space-around;font-size:12px;margin-top:40px;font-family:"League Spartan",sans-serif}
.post-meta span{color:var(--gold)}
.post-title{text-align:center;font-size:15px;line-height:34px;margin-top:8px}
.arrow{font-size:30px;color:var(--gold-text);top:3284px}
/* footer */
.footer{left:0;top:3648px;width:1200px;height:327px;background:#1a1918}
.foot-col{top:3700px;font-size:13px;line-height:31px;font-family:"League Spartan",sans-serif;text-transform:uppercase}
.copyright{left:0;top:3936px;width:1200px;text-align:center;font-size:13px;font-family:"League Spartan",sans-serif}
</style>
</head>
<body>

<header>
  <div class="abs brand" style="left:90px;top:44px"><span class="brand-dot"></span><span class="brand-name">Tessaro Mobile</span></div>
  <nav class="abs site-nav">
    <span class="active">Home</span><span>Bring your own phone</span><span>Coverage check</span><span>About us</span><span>Support</span><span>Blog</span>
  </nav>
  <div class="abs account-btn">MY ACCOUNT</div>
  <div class="abs lang">EN ▾</div>
</header>

<section class="hero">
  <div class="abs hero-card"></div>
  <div class="abs hero-kicker head">Your mobile, your way</div>
  <h1 class="abs hero-title head">Connect to the future with our <span class="gold">5G networks</span> at Tessaro Mobile</h1>
  <div class="abs countdown">
    <div class="cd-unit"><div class="cd-num">09</div><div class="cd-label">DAYS</div></div><div class="cd-sep">:</div>
    <div class="cd-unit"><div class="cd-num">19</div><div class="cd-label">HOURS</div></div><div class="cd-sep">:</div>
    <div class="cd-unit"><div class="cd-num">45</div><div class="cd-label">MINUTES</div></div><div class="cd-sep">:</div>
    <div class="cd-unit"><div class="cd-num">02</div><div class="cd-label">SECOND</div></div>
  </div>
  <div class="abs hero-art" role="img" aria-label="Smiling woman sitting with a smartphone beside a large phone showing the brand mascot"></div>
</section>

<section class="features">
  <div class="abs feature head" style="left:111px">
    <svg viewBox="0 0 64 64" fill="none" stroke="#c2a462" stroke-width="2"><rect x="12" y="26" width="30" height="24"/><path d="M12 34h30M27 26v8"/><circle cx="44" cy="14" r="6"/></svg>
    <div>Free 2-day shipping,<br>seriously!</div></div>
  <div class="abs feature highlight head" style="left:359px" role="img" aria-label="Man reviewing paperwork at a desk">
    <svg viewBox="0 0 64 64" fill="none" stroke="#fff" stroke-width="2"><rect x="14" y="20" width="28" height="30"/><path d="M20 30h16M20 38h12"/><circle cx="44" cy="20" r="9"/><path d="M40 20l3 3 6-6"/></svg>
    <div>No credit checks, no<br>stress</div></div>
  <div class="abs feature head" style="left:606px">
    <svg viewBox="0 0 64 64" fill="none" stroke="#c2a462" stroke-width="2"><path d="M8 44a24 24 0 0 1 48 0"/><path d="M32 44l12-16"/><circle cx="32" cy="44" r="4"/></svg>
    <div>5G speed at full<br>throttle!</div></div>
  <div class="abs feature head" style="left:853px">
    <svg viewBox="0 0 64 64" fill="none" stroke="#c2a462" stroke-width="2"><rect x="14" y="8" width="30" height="40"/><path d="M20 18h18M20 26h18M20 34h12"/><path d="M30 50l8-6 12 4"/></svg>
    <div>Zero annual<br>contracts, zero<br>hassles!</div></div>
</section>

<section class="check">
  <div class="abs check-band"></div>
  <h2 class="abs section-title head" style="top:970px">Check <span class="gold">everything</span> you need</h2>
  <div class="abs mascot" style="left:116px;top:964px;width:108px;height:139px" role="img" aria-label="Brand mascot cartoon fox holding a phone"></div>
  <div class="abs check-panel"><div class="check-left"></div><div class="check-right"></div></div>
  <div class="abs head gold" style="left:353px;top:1088px;font-size:17px">Coverage checker</div>
  <div class="abs" style="left:275px;top:1134px;font-size:15px">Enter your ZIP code to get started</div>
  <div class="abs head gold" style="left:635px;top:1088px;font-size:17px">Device checker</div>
  <div class="abs" style="left:635px;top:1134px;font-size:15px">Lorem ipsum dolor sit amet, consectetur</div>
  <div class="abs check-input" style="left:302px;width:296px;background:var(--gold-deep);color:#f1e7cc">CHECK YOUR COVERAGE</div>
  <div class="abs check-input" style="left:598px;width:298px;background:#fff;color:#9a9a9a">CHECK YOUR DEVICE</div>
</section>

<section class="steps">
  <h2 class="abs section-title head" style="top:1424px">Easy <span class="gold">activation</span> process</h2>
  <div class="abs step-num" style="left:111px;top:1494px">01</div>
  <div class="abs step-num" style="left:111px;top:1740px">02</div>
  <div class="abs step-num" style="left:1004px;top:1494px">03</div>
  <div class="abs step-num" style="left:1004px;top:1740px">04</div>
  <svg class="abs" style="left:372px;top:1506px" width="66" height="76" viewBox="0 0 66 76" fill="none" stroke="#c2a462" stroke-width="2"><rect x="4" y="2" width="36" height="68" rx="4"/><path d="M14 50v-8M20 50v-12M26 50v-16"/><circle cx="50" cy="60" r="12"/><path d="M44 60l4 4 8-8"/></svg>
  <svg class="abs" style="left:372px;top:1755px" width="66" height="76" viewBox="0 0 66 76" fill="none" stroke="#c2a462" stroke-width="2"><rect x="22" y="2" width="32" height="56" rx="4"/><path d="M10 74c0-20 6-30 16-30"/></svg>
  <svg class="abs" style="left:768px;top:1506px" width="72" height="76" viewBox="0 0 72 76" fill="none" stroke="#c2a462" stroke-width="2"><rect x="2" y="4" width="46" height="66" rx="3"/><path d="M12 20h26M12 34h26M12 48h18"/><path d="M40 66l24-26 6 6-24 26h-6z"/></svg>
  <svg class="abs" style="left:768px;top:1755px" width="72" height="76" viewBox="0 0 72 76" fill="none" stroke="#c2a462" stroke-width="2"><rect x="2" y="4" width="56" height="56" rx="3"/><path d="M2 16h56M12 28h30M12 40h24"/><circle cx="56" cy="60" r="12"/><path d="M50 60l4 4 8-8"/></svg>

  <div class="abs head step-title" style="right:766px;top:1602px;text-align:right">Check coverage in your area</div>
  <div class="abs step-desc" style="right:766px;top:1644px;text-align:right">Lorem ipsum dolor sit amet, consectetur<br>adipiscing elit, sed do eiusmod tempor incididunt</div>
  <div class="abs head step-title" style="right:766px;top:1850px;text-align:right">Bring your phone or get<br>a new one</div>
  <div class="abs step-desc" style="right:766px;top:1926px;text-align:right">Lorem ipsum dolor sit amet, consectetur</div>
  <div class="abs head step-title" style="left:768px;top:1602px">Choose the plan you like best</div>
  <div class="abs step-desc" style="left:768px;top:1644px">Lorem ipsum dolor sit amet, consectetur<br>adipiscing elit, sed do eiusmod tempor incididunt</div>
  <div class="abs head step-title" style="left:768px;top:1850px">Place your order and activate<br>plan</div>
  <div class="abs step-desc" style="left:768px;top:1926px">Lorem ipsum dolor sit amet, consectetur</div>

  <div class="abs phone-frame"></div>
  <div class="abs brand" style="left:506px;width:188px;top:1662px;justify-content:center"><span class="brand-dot"></span><span class="brand-name" style="font-size:16px">Tessaro Mobile</span></div>
  <div class="abs mascot" style="left:552px;top:1716px;width:96px;height:140px" role="img" aria-label="Brand mascot cartoon fox holding a phone"></div>
</section>

<section class="reviews">
  <div class="abs review-band"></div>
  <h2 class="abs section-title head" style="top:2083px">Tessaro Mobile is the <span class="gold">best!</span></h2>
  <div class="abs review" style="left:143px"><div class="stars">★★★★★</div><p>I've been using Veradilo for a few months now, and I have to say, their connection is solid!...</p><div class="reviewer"><div class="avatar"></div>MARLA QUENTE</div></div>
  <div class="abs review" style="left:452px"><div class="stars">★★★★★</div><p>Veradilo has been a game-changer for me when it comes to saving money on my phone...</p><div class="reviewer"><div class="avatar"></div>RUFO ALVAREN</div></div>
  <div class="abs review" style="left:763px"><div class="stars">★★★★★</div><p>One thing I love about Veradilo is their amazing customer service in both English and Spanish...</p><div class="reviewer"><div class="avatar"></div>NADIA THRELK</div></div>
</section>

<section class="questions">
  <h2 class="abs section-title head" style="top:2566px">The answer to all your <span class="gold">questions</span></h2>
  <div class="abs faq" style="left:126px;top:2646px"><span>Lorem ipsum dolor sit amet, consectetur ?</span><svg width="16" height="16" viewBox="0 0 16 16" fill="none" stroke="#fff" stroke-width="1.2"><circle cx="8" cy="8" r="7"/><path d="M8 4.5v7M4.5 8h7"/></svg></div>
  <div class="abs faq" style="left:126px;top:2732px"><span>Lorem ipsum dolor sit amet, consectetur ?</span><svg width="16" height="16" viewBox="0 0 16 16" fill="none" stroke="#fff" stroke-width="1.2"><circle cx="8" cy="8" r="7"/><path d="M8 4.5v7M4.5 8h7"/></svg></div>
  <div class="abs faq" style="left:126px;top:2819px"><span>Lorem ipsum dolor sit amet, consectetur ?</span><svg width="16" height="16" viewBox="0 0 16 16" fill="none" stroke="#fff" stroke-width="1.2"><circle cx="8" cy="8" r="7"/><path d="M8 4.5v7M4.5 8h7"/></svg></div>
  <div class="abs faq" style="left:126px;top:2905px"><span>Lorem ipsum dolor sit amet, consectetur ?</span><svg width="16" height="16" viewBox="0 0 16 16" fill="none" stroke="#fff" stroke-width="1.2"><circle cx="8" cy="8" r="7"/><path d="M8 4.5v7M4.5 8h7"/></svg></div>
  <div class="abs faq" style="left:641px;top:2646px"><span>Lorem ipsum dolor sit amet, consectetur ?</span><svg width="16" height="16" viewBox="0 0 16 16" fill="none" stroke="#fff" stroke-width="1.2"><circle cx="8" cy="8" r="7"/><path d="M8 4.5v7M4.5 8h7"/></svg></div>
  <div class="abs faq" style="left:641px;top:2732px"><span>Lorem ipsum dolor sit amet, consectetur ?</span><svg width="16" height="16" viewBox="0 0 16 16" fill="none" stroke="#fff" stroke-width="1.2"><circle cx="8" cy="8" r="7"/><path d="M8 4.5v7M4.5 8h7"/></svg></div>
  <div class="abs faq" style="left:641px;top:2819px"><span>Lorem ipsum dolor sit amet, consectetur ?</span><svg width="16" height="16" viewBox="0 0 16 16" fill="none" stroke="#fff" stroke-width="1.2"><circle cx="8" cy="8" r="7"/><path d="M8 4.5v7M4.5 8h7"/></svg></div>
  <div class="abs faq" style="left:641px;top:2905px"><span>Lorem ipsum dolor sit amet, consectetur ?</span><svg width="16" height="16" viewBox="0 0 16 16" fill="none" stroke="#fff" stroke-width="1.2"><circle cx="8" cy="8" r="7"/><path d="M8 4.5v7M4.5 8h7"/></svg></div>
  <div class="abs faq-btn head">View more questions</div>
  <div class="abs mascot" style="left:80px;top:2961px;width:108px;height:146px" role="img" aria-label="Brand mascot cartoon fox giving a thumbs up"></div>
</section>

<section class="posts">
  <h2 class="abs section-title head" style="top:3115px">Tessaro Mobile <span class="gold">connection</span></h2>
  <div class="abs arrow" style="left:36px">‹</div>
  <div class="abs arrow" style="left:1133px">›</div>
  <article class="abs post" style="left:111px"><div class="post-img" style="background:linear-gradient(135deg,#dfe6ee,#5a6f88 60%,#1a2230)" role="img" aria-label="Hands on a laptop with a glowing global network overlay"></div>
    <div class="post-meta"><div><span>●</span> OWEN PARDELL</div><div><span>▦</span> 21/08/2024</div></div>
    <div class="post-title head">Lorem ipsum dolor sit amet elit<br>sed do eiusmod</div></article>
  <article class="abs post" style="left:442px"><div class="post-img" style="background:linear-gradient(135deg,#a9d6ee,#3c87b8 55%,#0f3a5a)" role="img" aria-label="Hand holding a smartphone with glowing signal rings"></div>
    <div class="post-meta"><div><span>●</span> OWEN PARDELL</div><div><span>▦</span> 21/08/2024</div></div>
    <div class="post-title head">Lorem ipsum dolor sit amet elit<br>sed do eiusmod</div></article>
  <article class="abs post" style="left:773px"><div class="post-img" style="background:linear-gradient(180deg,#0e1e3a,#233f6e 60%,#324e78)" role="img" aria-label="City skyline at night with connected network lines"></div>
    <div class="post-meta"><div><span>●</span> OWEN PARDELL</div><div><span>▦</span> 21/08/2024</div></div>
    <div class="post-title head">Lorem ipsum dolor sit amet elit<br>sed do eiusmod</div></article>
</section>

<footer>
  <div class="abs footer"></div>
  <div class="abs mascot" style="left:1036px;top:3531px;width:108px;height:139px" role="img" aria-label="Brand mascot cartoon fox holding a phone"></div>
  <div class="abs brand" style="left:131px;top:3760px"><span class="brand-dot" style="width:14px;height:14px"></span><span class="brand-name" style="font-size:22px">Tessaro Mobile</span></div>
  <div class="abs foot-col" style="left:412px">Home<br>Bring your own phone<br>Coverage check<br>About us<br>Support<br>Blog</div>
  <div class="abs foot-col" style="left:708px">My account<br>Plans<br>Phones<br>Add data</div>
  <div class="abs foot-col" style="left:925px">Why Tessaro Mobile<br>Contact<br>Coverage info<br>Reviews<br>Blog</div>
  <div class="abs copyright">©2025 COPYRIGHTS - ALL RIGHTS RESERVED</div>
</footer>

</body>
</html>
```